Design a New Business Card for Our Company

We are looking for fresh, unique, and a modern business card that reflects our roots as digital marketing agency focused on SEM.

Industry/Entity Type

Marketing

Contact Information for Business Card

looking for very unique out of the box designs. clean and modern that compliments our logo

Requirements
Must have
• colors should match our logo
• Front should have name, address, email, and phone/fax of the person, phone/fax are the same number
• back should have our url

```html
<!DOCTYPE html>
<html lang="en">
<head>
<meta charset="utf-8">
<title>Brightpath Media – Business Card</title>
<link rel="stylesheet" href="https://fonts.googleapis.com/css2?family=Open+Sans:wght@400;600;700&display=swap">
<style>
  :root {
    --stage: #e9e7e4;
    --card-grey: #b1b1b1;
    --stripe-grey: #a9a9a9;
    --brand-blue: #5693d1;
    --white: #ffffff;
    --icon-bg: #c9ccd1;
    --icon-ink: #6f7680;
    --shadow: rgba(0, 0, 0, 0.18);
  }
  * { box-sizing: border-box; margin: 0; padding: 0; }
  html, body { width: 1200px; height: 675px; overflow: hidden; }
  body {
    background: var(--stage);
    font-family: "Open Sans", Arial, sans-serif;
    position: relative;
  }
  .card {
    position: absolute;
    top: 189px;
    width: 520px;
    height: 297px;
    box-shadow: 0 6px 18px var(--shadow);
    overflow: hidden;
  }
  /* Back side */
  .card-back { left: 50px; background: var(--card-grey); }
  .card-back .brand {
    position: absolute;
    right: 34px;
    bottom: 62px;
    display: flex;
    align-items: center;
    gap: 10px;
    color: var(--white);
    font-weight: 700;
    font-size: 40px;
    letter-spacing: -1px;
    line-height: 1;
  }
  .card-back .url {
    position: absolute;
    right: 36px;
    bottom: 34px;
    color: var(--white);
    font-size: 15px;
    font-weight: 400;
  }
  /* Front side */
  .card-front { left: 630px; background: var(--white); }
  .card-front .panel { position: absolute; inset: 0; }
  .card-front .brand {
    position: absolute;
    left: 30px;
    top: 108px;
    display: flex;
    align-items: center;
    gap: 10px;
    color: var(--brand-blue);
    font-weight: 700;
    font-size: 34px;
    letter-spacing: -1px;
    line-height: 1;
  }
  .brand-dot {
    width: 22px;
    height: 22px;
    border-radius: 50%;
    background: currentColor;
    flex: none;
  }
  .contact {
    position: absolute;
    right: 26px;
    top: 92px;
    text-align: right;
    color: var(--white);
    font-size: 13px;
    line-height: 1.3;
  }
  .contact .name { font-size: 16px; font-weight: 700; }
  .contact .role { margin-bottom: 8px; }
  .contact .address { margin-bottom: 14px; }
  .contact-line {
    display: flex;
    justify-content: flex-end;
    align-items: center;
    gap: 6px;
    margin-bottom: 2px;
  }
  .icon {
    width: 15px;
    height: 15px;
    border-radius: 3px;
    background: var(--icon-bg);
    display: block;
    flex: none;
  }
</style>
</head>
<body>

<section class="card card-back" aria-label="Card back">
  <div class="brand"><span class="brand-dot" aria-hidden="true"></span>brightpath</div>
  <p class="url">www.brightpathmedia.com</p>
</section>

<section class="card card-front" aria-label="Card front">
  <svg class="panel" viewBox="0 0 520 297" width="520" height="297" aria-hidden="true">
    <polygon points="328,0 340,0 356,118 176,297 160,297 344,118" fill="var(--stripe-grey)"/>
    <polygon points="340,0 520,0 520,297 176,297 356,118" fill="var(--brand-blue)"/>
  </svg>

  <div class="brand"><span class="brand-dot" aria-hidden="true"></span>brightpath</div>

  <div class="contact">
    <p class="name">Dana Whitfield</p>
    <p class="role">Owner</p>
    <p class="address">N. 1 Cedar Lane, Suite 100,<br>Larkfield, WA 55555</p>

    <p class="contact-line">555.010.2040
      <svg class="icon" viewBox="0 0 15 15" aria-label="Phone"><path d="M4 3.5h2l.8 2.2-1.2.8a6 6 0 0 0 2.9 2.9l.8-1.2 2.2.8v2a1 1 0 0 1-1 1A8 8 0 0 1 3 4.5a1 1 0 0 1 1-1z" fill="var(--icon-ink)"/></svg>
    </p>
    <p class="contact-line">555.010.2040
      <svg class="icon" viewBox="0 0 15 15" aria-label="Fax"><rect x="5" y="2.5" width="5" height="3" fill="var(--icon-ink)"/><rect x="3" y="6" width="9" height="5" rx="1" fill="var(--icon-ink)"/><rect x="5" y="9.5" width="5" height="3" fill="var(--white)"/></svg>
    </p>
    <p class="contact-line">info@brightpathmedia.com
      <svg class="icon" viewBox="0 0 15 15" aria-label="Email"><rect x="3" y="4.5" width="9" height="6" fill="var(--icon-ink)"/><path d="M3 4.5l4.5 3.5 4.5-3.5" stroke="var(--white)" stroke-width="1" fill="none"/></svg>
    </p>
    <p class="contact-line">www.brightpathmedia.com
      <svg class="icon" viewBox="0 0 15 15" aria-label="Website"><circle cx="7.5" cy="7.5" r="4.5" fill="none" stroke="var(--icon-ink)" stroke-width="1.2"/><ellipse cx="7.5" cy="7.5" rx="2" ry="4.5" fill="none" stroke="var(--icon-ink)" stroke-width="1"/><line x1="3" y1="7.5" x2="12" y2="7.5" stroke="var(--icon-ink)" stroke-width="1"/></svg>
    </p>
  </div>
</section>

</body>
</html>
```